International business needs business cards

Our company, DRV Ventures Inc. is in the business of supplying a range construction products with particular emphasis on CEMENT. We have developed our own brand - TORVAN SUPPLIES - with which to infiltrate the market. We are launching our brand of cement (TORVAN Type IS Cement) into the Caribbean which is unlike anything this market has ever seen. A monopoly has existed here for the past 60-odd years and the market has now opened to allow the importation of other brands and consumers are anxious and ready for change/improvement. We are very excited to be launching and want to make a great first impression. We will be conducting workshops and seminars (from government level to the hardware store owners) and we want our business card to give us the strong, confident introduction that we need.

Target Market(s)

construction; builders; engineers; home owners

Industry/Entity Type

Construction

Contact Information for Business Card

Marisol Depree
CEO
cell # 1 555 4180736
Ground floor,Lindell Plaza Suite 2734
George Town,Grand Cayman
Cayman Islands,KY1-4823
EMAIL: m.depree@drvventuresinc.example
web site drvventuresinc.example

COMPANY: skype info drv.ventures.example

second card
Yvette Brannock-Depree
CFO
CELL# 1 555 607 3941
George Town,Grand Cayman
Cayman Islands,KY1-4823
EMAIL: y.brannockdepree@drvventuresinc.example
website drvventuresinc.example

Requirements
Must have
• Business cards must display BOTH logos - DRV is the company and TORVAN is the brand.

```html
<!DOCTYPE html>
<html lang="en">
<head>
<meta charset="utf-8">
<title>DRV Ventures Inc. – Business Card</title>
<link rel="stylesheet" href="https://fonts.googleapis.com/css2?family=Open+Sans:wght@400;600;700&display=swap">
<style>
  :root {
    --page-bg: #2b2b2b;
    --card-black: #050505;
    --card-white: #ffffff;
    --brand-red: #8b1a1e;
    --ink: #111111;
    --ink-soft: #222222;
    --silver: #bdbdbd;
    --silver-dim: #6a6a6a;
  }
  * { box-sizing: border-box; margin: 0; padding: 0; }
  html, body {
    width: 1200px; height: 900px; overflow: hidden;
    background: var(--page-bg);
    font-family: "Open Sans", Arial, sans-serif;
  }
  .stage { position: relative; width: 1200px; height: 900px; }
  .card {
    position: absolute; width: 660px; height: 377px;
    box-shadow: 0 14px 30px rgba(0,0,0,0.45);
  }

  /* Back: brand side */
  .card-back { left: 110px; top: 50px; background: var(--card-black); }
  .brand-mark {
    position: absolute; left: 0; right: 0; top: 110px;
    display: flex; align-items: center; justify-content: center; gap: 16px;
  }
  .brand-mark .brand-dot {
    width: 40px; height: 40px; border-radius: 50%;
    background: var(--silver-dim);
  }
  .brand-mark .brand-name {
    font-weight: 700; font-size: 56px; letter-spacing: 8px; color: var(--silver);
  }
  .back-web {
    position: absolute; left: 0; right: 0; top: 268px;
    display: flex; justify-content: center; align-items: center; gap: 8px;
    color: #ffffff; font-size: 17px; font-weight: 400;
  }
  .back-web .web-dot { width: 14px; height: 14px; border-radius: 50%; background: #ffffff; }

  /* Front: contact side */
  .card-front { left: 430px; top: 470px; background: var(--card-white); }
  .company-mark {
    position: absolute; right: 60px; top: 48px;
    display: flex; align-items: center; gap: 12px;
  }
  .company-mark .company-square { width: 78px; height: 78px; background: var(--brand-red); }
  .company-mark .company-name {
    font-weight: 700; font-size: 30px; color: var(--ink); line-height: 1.05;
  }
  .contact {
    position: absolute; left: 48px; bottom: 40px; color: var(--ink-soft);
  }
  .contact .person-name { font-weight: 700; font-size: 26px; color: var(--ink); letter-spacing: 0.5px; }
  .contact .person-title { font-weight: 600; font-size: 15px; color: var(--brand-red); margin: 2px 0 8px; }
  .contact .address { font-weight: 600; font-size: 15px; line-height: 1.3; margin-bottom: 8px; }
  .contact .lines { list-style: none; font-weight: 600; font-size: 15px; line-height: 1.35; }
  .contact .lines li { display: flex; align-items: center; gap: 8px; }
  .contact .lines svg { width: 13px; height: 13px; flex: none; }
</style>
</head>
<body>
<main class="stage">

  <section class="card card-back" aria-label="Business card back">
    <div class="brand-mark">
      <span class="brand-dot"></span>
      <span class="brand-name">TORVAN</span>
    </div>
    <div class="back-web">
      <span class="web-dot"></span>
      <span>drv.ventures.example</span>
    </div>
  </section>

  <section class="card card-front" aria-label="Business card front">
    <div class="company-mark">
      <span class="company-square"></span>
      <span class="company-name">DRV Ventures Inc.</span>
    </div>

    <div class="contact">
      <p class="person-name">MARISOL DEPREE</p>
      <p class="person-title">CEO</p>
      <p class="address">Ground floor,Lindell Plaza Suite 2734<br>George Town,Grand Cayman<br>Cayman Islands,KY1-4823</p>
      <ul class="lines">
        <li>
          <svg viewBox="0 0 16 16" aria-hidden="true"><path fill="#8b1a1e" d="M3.6 1.5l2.3 2.6-1.3 1.8c.9 2 2.5 3.6 4.5 4.5l1.8-1.3 2.6 2.3-1.3 2.3C7 13.5 2.5 9 1.3 2.8z"/></svg>
          1 555 4180736
        </li>
        <li>
          <svg viewBox="0 0 16 16" aria-hidden="true"><rect x="1.5" y="3.5" width="13" height="9" fill="none" stroke="#8b1a1e" stroke-width="1.6"/><path d="M1.5 3.5l6.5 5 6.5-5" fill="none" stroke="#8b1a1e" stroke-width="1.6"/></svg>
          m.depree@drvventuresinc.example
        </li>
        <li>
          <svg viewBox="0 0 16 16" aria-hidden="true"><circle cx="8" cy="8" r="6.5" fill="none" stroke="#8b1a1e" stroke-width="1.5"/><path d="M1.5 8h13M8 1.5c-3 3.5-3 9.5 0 13M8 1.5c3 3.5 3 9.5 0 13" fill="none" stroke="#8b1a1e" stroke-width="1.2"/></svg>
          www.drvventuresinc.example
        </li>
      </ul>
    </div>
  </section>

</main>
</body>
</html>
```